Corvane Capital Business Cards

These are professional business cards that are for my family office.
Put fake emails and phone numbers as of now until I finalize those components. This family office controls my families investments, assets, and future. The cards should be professional.
..
.
.
.
I just uploaded another variation of a logo I would like to see as a business card to I am inbeteen which logo to use

Target Market(s)

business

Industry/Entity Type

business

Contact Information for Business Card

Professional, wealth related, finance related.

Requirements
Must have
• Logo

```html
<!DOCTYPE html>
<html lang="en">
<head>
<meta charset="utf-8">
<title>Corvane Capital Business Cards</title>
<link href="https://fonts.googleapis.com/css2?family=Playfair+Display:wght@400&family=Lora:wght@700&family=Tinos&display=swap" rel="stylesheet">
<style>
  :root {
    --gold: #c6ad70;
    --ink: #0b0b0b;
    --paper: #ffffff;
    --backdrop: #ecebeb;
  }
  * { margin: 0; padding: 0; box-sizing: border-box; }
  html, body { width: 1200px; height: 716px; overflow: hidden; background: var(--backdrop); }
  .sheet { position: relative; width: 1200px; height: 716px; }
  .card {
    position: absolute; left: 369px; width: 461px; height: 263px; overflow: hidden;
  }
  .card--front { top: 94px; background: var(--gold); }
  .card--back { top: 385px; background: var(--paper); }

  .brand-mark { position: absolute; left: 50%; transform: translateX(-50%); }
  .card--front .brand-mark { top: 78px; width: 56px; height: 56px; background: var(--paper); }
  .card--back .brand-mark { top: 32px; width: 36px; height: 36px; background: var(--gold); }

  .brand-name {
    font-family: "Playfair Display", Georgia, serif; font-weight: 400; line-height: 1;
    letter-spacing: 0.01em; white-space: nowrap; text-align: center;
    position: absolute; left: 0; right: 0;
  }
  .card--front .brand-name { top: 150px; font-size: 37px; color: var(--paper); }
  .card--back .brand-name { top: 77px; font-size: 24px; color: var(--ink); }

  .holder { position: absolute; left: 0; right: 0; top: 140px; text-align: center; }
  .holder-name { font-family: "Lora", Georgia, serif; font-weight: 700; font-size: 17px; color: var(--ink); }
  .holder-name .surname { color: var(--gold); }
  .holder-role {
    display: flex; align-items: center; justify-content: center; gap: 7px; margin-top: 1px;
    font-family: "Tinos", "Times New Roman", serif; font-size: 14px; color: var(--ink);
  }
  .role-rule { width: 101px; height: 5px; }

  .contact { position: absolute; left: 0; right: 0; top: 196px; font-family: "Tinos", "Times New Roman", serif; font-size: 14px; color: var(--ink); }
  .contact-row { display: flex; align-items: center; justify-content: center; gap: 5px; height: 19px; }
  .contact-icon { width: 13px; height: 13px; }

  .footer-band { position: absolute; left: 0; bottom: 0; width: 461px; height: 18px; }
</style>
</head>
<body>
<main class="sheet">
  <section class="card card--front" aria-label="Card front">
    <span class="brand-mark" aria-hidden="true"></span>
    <p class="brand-name">CORVANE CAPITAL</p>
  </section>

  <section class="card card--back" aria-label="Card back">
    <span class="brand-mark" aria-hidden="true"></span>
    <p class="brand-name">CORVANE CAPITAL</p>

    <div class="holder">
      <p class="holder-name">Daniel <span class="surname">Hale</span></p>
      <p class="holder-role">
        <svg class="role-rule" viewBox="0 0 101 5"><polygon points="0,2.5 101,0 101,5" fill="var(--gold)"/></svg>
        Founder
        <svg class="role-rule" viewBox="0 0 101 5"><polygon points="0,0 101,2.5 0,5" fill="var(--gold)"/></svg>
      </p>
    </div>

    <div class="contact">
      <p class="contact-row">
        <svg class="contact-icon" viewBox="0 0 13 13" aria-hidden="true">
          <rect width="13" height="13" fill="var(--gold)"/>
          <path d="M3 6 Q6.5 2.5 10 6 L9 7 L8 6 L5 6 L4 7 Z M4.5 7.5 H8.5 L9.5 10 H3.5 Z" fill="#fff"/>
        </svg>
        555-014-2290
      </p>
      <p class="contact-row">
        <svg class="contact-icon" viewBox="0 0 13 13" aria-hidden="true">
          <rect width="13" height="13" fill="var(--gold)"/>
          <rect x="2.5" y="3.5" width="8" height="6" fill="none" stroke="#fff" stroke-width="0.9"/>
          <path d="M2.5 3.5 L6.5 7 L10.5 3.5" fill="none" stroke="#fff" stroke-width="0.9"/>
        </svg>
        info@corvanemail.com
      </p>
    </div>

    <svg class="footer-band" viewBox="0 0 461 18" preserveAspectRatio="none" aria-hidden="true">
      <polygon points="0,0 233,0 215,18 0,18" fill="var(--gold)"/>
      <polygon points="238,0 461,0 461,18 220,18" fill="var(--ink)"/>
    </svg>
  </section>
</main>
</body>
</html>
```